Creation of brand identity and website "Tandem K"

I am currently seeking an brand, identity and web design for a new project called Tandem K. This is a brand new concept from scratch and you have free-reign on the whole design process, taking into account my preference below.

Must include the name "Tandem K", or "Tandem K: Or the year I woke Up". Kudos is this forms part of the brands logo

Design that can be easily scaled to potentially include: a blog, timeline and vlogs.

Minimal but effective use of colour (however any colours and combinations permitted

Use of icons/graphics over text wherever possible

Minimal use of frames and borders

I appreciate this is a fairly wide scope so please contact me on marblefinch@postwillow.com with any questions or more information on what the project is.

Target Market(s)

Male and Female 20-40
Blog readers
Selfhelp

Industry/Entity Type

Seeking

Number of Pages Required

1 page

Font styles to use
Serif
Sans Serif

Requirements
Must have
• It is in effect a blog design, so about me section, recent blog / archived posts, reader comments / Q and A section.
• A coded design would be appreciated to make my life easier however I have left the design as uncoded as getting the right design matters more to me and I want to keep the project open to as many designers as possible
Nice to have
• See project description for other details and please ask if you need anything else :)
Should not have
• Mustn't be cluttered or feel fussy
• Promote icons over text
• Frames / multiple borders

```html
<!DOCTYPE html>
<html lang="en">
<head>
<meta charset="utf-8">
<title>Tandem K</title>
<link rel="stylesheet" href="https://fonts.googleapis.com/css2?family=Montserrat:wght@400;600;700&family=Lato:wght@400;700&display=swap">
<style>
:root{
  --orange:#ff9900;
  --orange-dark:#f08c00;
  --ink:#222;
  --text:#444;
  --muted:#666;
  --dark:#2f2f2f;
  --page:#f5f5f5;
  --line:#e2e2e2;
  --white:#fff;
}
*{box-sizing:border-box;margin:0;padding:0}
html,body{width:1200px;height:2381px;overflow:hidden}
body{position:relative;background:var(--page);font-family:"Lato",sans-serif;color:var(--text)}
.abs{position:absolute}
.site-header{left:0;top:0;width:1200px;height:75px;background:var(--dark)}
.brand{left:84px;top:20px;font:700 28px "Montserrat",sans-serif;color:var(--white)}
.nav{left:449px;top:0;display:flex;height:75px}
.nav a{display:flex;align-items:center;justify-content:center;padding:0 11px;font:600 14px "Montserrat",sans-serif;color:var(--white);text-decoration:none;white-space:nowrap}
.nav a.active{background:var(--orange);width:103px;margin-right:10px}
.header-social{left:1008px;top:30px;display:flex;gap:18px}
.header-social span{width:14px;height:14px;border-radius:50%;background:var(--white)}
.hero{left:0;top:75px;width:1200px;height:436px;background:linear-gradient(180deg,#7a3a08 0%,#c8620c 35%,#e07a12 60%,#8a3a06 100%)}
.hero-title{left:83px;top:188px;width:480px;font:700 24px/1.33 "Montserrat",sans-serif;color:var(--white)}
.hero-dash{left:83px;top:306px;display:flex;gap:6px}
.hero-dash span{width:16px;height:3px;background:var(--white)}
.card{background:var(--white);border:1px solid var(--line)}
.featured{left:84px;top:556px;width:711px;height:460px}
.featured-img{height:264px;background:linear-gradient(180deg,#f2b24a 0%,#f7c766 55%,#e9a43c 100%)}
.meta{display:flex;align-items:center;font-size:12px;color:var(--ink);white-space:nowrap}
.meta svg{margin-right:6px}
.featured .meta{position:absolute;top:288px;left:14px;width:690px;font-size:14px}
.featured h2{position:absolute;top:322px;left:14px;font:700 20px "Montserrat",sans-serif;color:var(--ink)}
.featured p{position:absolute;top:356px;left:14px;width:560px;font-size:15px;line-height:1.4;color:var(--ink)}
.btn{display:inline-block;background:var(--orange);color:var(--white);font:700 13px "Montserrat",sans-serif;letter-spacing:.5px;text-decoration:none}
.featured .btn{position:absolute;top:408px;left:13px;width:120px;height:34px;line-height:34px;text-align:center}
.rule{left:84px;width:711px;height:1px;background:var(--line)}
.post{width:349px;height:200px}
.post h3{position:absolute;top:20px;left:13px;font:700 16px "Montserrat",sans-serif;color:var(--ink);white-space:nowrap}
.post .meta{position:absolute;top:55px;left:13px;width:305px;font-size:12px}
.post .thumb{position:absolute;top:91px;left:14px;width:81px;height:81px}
.post p{position:absolute;top:91px;left:110px;width:228px;font-size:12.4px;line-height:1.52;color:var(--ink)}
.post p a,.more{color:var(--orange);text-decoration:none}
.sp{margin-left:auto}
.gap{margin-left:26px}
.widget{left:836px;width:280px}
.widget h4{font:700 15px "Montserrat",sans-serif;color:var(--ink)}
.newsletter{top:557px;height:137px;padding:12px 13px}
.email{margin-top:13px;height:34px;border:1px solid var(--line);font-size:12px;color:#999;padding:10px 12px}
.newsletter .btn{margin-top:14px;height:34px;line-height:34px;padding:0 13px;font-size:11px}
.tabs-box{top:727px;height:341px}
.tabs{display:flex;height:36px;background:#e6e6e6;font:600 11px "Montserrat",sans-serif;color:var(--ink);white-space:nowrap}
.tabs span{display:flex;align-items:center;justify-content:center}
.tabs span:nth-child(1){width:89px}
.tabs span:nth-child(2){width:124px}
.tabs span:nth-child(3){flex:1}
.tabs span.on{background:var(--orange);color:var(--white)}
.pop{display:flex;align-items:center;margin:9px 12px 0}
.pop:first-of-type{margin-top:26px}
.pop .ph{width:73px;height:73px;flex:none}
.pop p{margin-left:18px;width:155px;font-size:12.5px;line-height:1.4;color:var(--ink)}
.view-all{position:absolute;right:12px;bottom:18px;font:700 12px "Lato",sans-serif;text-decoration:underline}
.follow{top:1098px;height:95px;border-top:6px solid #ddd;padding:10px 13px}
.follow-row{display:flex;justify-content:space-between;margin-top:14px}
.follow-row span{width:36px;height:36px;background:#9a9a9a}
.archives{top:1236px;height:221px;padding:10px 13px}
.archives ul{list-style:none;margin-top:8px}
.archives li{font:700 12.5px/15px "Lato",sans-serif;color:var(--ink);padding:5px 0 4px;border-bottom:1px solid #eee}
.archives li:last-child{border-bottom:0}
.tags{top:1490px;height:172px;padding:10px 13px}
.tag-list{display:flex;flex-wrap:wrap;gap:6px;margin-top:14px}
.tag-list span{background:var(--orange);color:var(--white);font:700 14px "Montserrat",sans-serif;height:31px;line-height:31px;padding:0 15px}
.ad{left:836px;top:1712px;width:280px;height:248px;background:linear-gradient(160deg,#5a4a3a 0%,#2a2320 55%,#141210 100%)}
.about{left:0;top:2000px;width:1200px;height:336px;background:var(--orange)}
.about-photo{left:146px;top:47px;width:252px;height:254px;border:3px solid #e2e2e2;background:linear-gradient(180deg,#b9c7cf 0%,#8fa2ad 60%,#6f8794 100%)}
.about h2{left:435px;top:58px;font:700 24px "Montserrat",sans-serif;color:var(--white)}
.about p{left:435px;top:98px;width:594px;font-size:13.4px;line-height:1.49;color:var(--white)}
.about .more{left:445px;top:272px;color:var(--white);font:700 15px "Montserrat",sans-serif}
.footer{left:0;top:2336px;width:1200px;height:45px;background:var(--dark);color:var(--white);font:600 11.5px "Montserrat",sans-serif;text-align:center;line-height:45px}
</style>
</head>
<body>
<svg width="0" height="0" style="position:absolute">
  <defs>
    <symbol id="i-cal" viewBox="0 0 12 12"><rect x="1" y="2" width="10" height="9" rx="1" fill="#ff9900"/><rect x="2" y="4.5" width="8" height="5.5" fill="#fff"/></symbol>
    <symbol id="i-com" viewBox="0 0 12 12"><path d="M6 1.5c3 0 5 1.7 5 3.8S9 9 6 9H5l-3 2 .7-2.6C1.6 7.8 1 6.6 1 5.3 1 3.2 3 1.5 6 1.5z" fill="#ff9900"/></symbol>
    <symbol id="i-share" viewBox="0 0 12 12"><path d="M7 2l4 3.5L7 9V7C4 7 2.5 8 1 10c.5-3.5 2.5-5.5 6-6V2z" fill="#ff9900"/></symbol>
    <symbol id="i-clock" viewBox="0 0 12 12"><circle cx="6" cy="6" r="5" fill="none" stroke="#ff9900" stroke-width="1.3"/><path d="M6 3v3.2l2 1.3" stroke="#ff9900" stroke-width="1.3" fill="none"/></symbol>
  </defs>
</svg>

<header class="site-header abs">
  <div class="brand abs">Tandem K</div>
  <nav class="nav abs">
    <a class="active" href="#">About Me</a>
    <a href="#">Recent Blog</a>
    <a href="#">Reader Comments</a>
    <a href="#">Contact Us</a>
  </nav>
  <div class="header-social abs"><span></span><span></span><span></span><span></span></div>
</header>

<section class="hero abs" role="img" aria-label="Girl running through a golden wheat field at sunset">
  <h1 class="hero-title abs">Lorem ipsum dolor sit amet, consectetuer adipiscing elit, sed nonummy nibh euismod</h1>
  <div class="hero-dash abs"><span></span><span></span><span></span></div>
</section>

<article class="card featured abs">
  <div class="featured-img" role="img" aria-label="Silhouette of a woman with raised arms against a golden sunset sky"></div>
  <div class="meta"><svg width="14" height="14"><use href="#i-clock"/></svg>MAY 18, 2015 &nbsp;|&nbsp; BY&nbsp;<b>Lorem Ipsum</b>
    <span style="margin-left:66px"></span><svg width="13" height="13"><use href="#i-cal"/></svg>June 18, 2016
    <span class="gap"></span><svg width="13" height="13"><use href="#i-com"/></svg>No Comments
    <span class="gap"></span>Share&nbsp;<svg width="13" height="13"><use href="#i-share"/></svg></div>
  <h2>Lorem Ipsum Dolor Sit Amet</h2>
  <p>Lorem ipsum dolor sit amet, consectetuer adipiscing elit, sed diam nonummy nibh euismod tincidunt ut laoreet dolore magna aliquam erat volutpat.</p>
  <a class="btn" href="#">READ MORE</a>
</article>

<div class="rule abs" style="top:1030px"></div>
<div class="rule abs" style="top:1266px"></div>
<div class="rule abs" style="top:1503px"></div>
<div class="rule abs" style="top:1739px"></div>

<article class="card post abs" style="left:84px;top:1049px"><h3>Lorem ipsum dolor sit amet consecit</h3><div class="meta"><svg width="12" height="12"><use href="#i-cal"/></svg>June 18, 2016<span class="gap"></span><svg width="12" height="12"><use href="#i-com"/></svg>No Comments<span class="sp">Share&nbsp;</span><svg width="12" height="12"><use href="#i-share"/></svg></div><div class="thumb" role="img" aria-label="Couple embracing outdoors" style="background:linear-gradient(135deg,#8a4a3a,#c98a6a)"></div><p>Lorem ipsum dolor sit amet, consecit adipiscing elit, sed do eiusmod tempor incidimen labore n dolorme laboris ni ut ullamc...... <a href="#">Read More</a></p></article>
<article class="card post abs" style="left:446px;top:1049px"><h3>Lorem ipsum dolor sit amet consecit</h3><div class="meta"><svg width="12" height="12"><use href="#i-cal"/></svg>June 18, 2016<span class="gap"></span><svg width="12" height="12"><use href="#i-com"/></svg>No Comments<span class="sp">Share&nbsp;</span><svg width="12" height="12"><use href="#i-share"/></svg></div><div class="thumb" role="img" aria-label="Red-haired woman in a sunny garden" style="background:linear-gradient(135deg,#c8d28a,#b8603a)"></div><p>Lorem ipsum dolor sit amet, consecit adipiscing elit, sed do eiusmod tempor incidimen labore n dolorme laboris ni ut ullamc...... <a href="#">Read More</a></p></article>

<article class="card post abs" style="left:84px;top:1285px"><h3>Lorem ipsum dolor sit amet consecit</h3><div class="meta"><svg width="12" height="12"><use href="#i-cal"/></svg>June 18, 2016<span class="gap"></span><svg width="12" height="12"><use href="#i-com"/></svg>No Comments<span class="sp">Share&nbsp;</span><svg width="12" height="12"><use href="#i-share"/></svg></div><div class="thumb" role="img" aria-label="Woman leaping in a yellow flower field" style="background:linear-gradient(180deg,#f0c040,#c89010)"></div><p>Lorem ipsum dolor sit amet, consecit adipiscing elit, sed do eiusmod tempor incidimen labore n dolorme laboris ni ut ullamc...... <a href="#">Read More</a></p></article>
<article class="card post abs" style="left:446px;top:1285px"><h3>Lorem ipsum dolor sit amet consecit</h3><div class="meta"><svg width="12" height="12"><use href="#i-cal"/></svg>June 18, 2016<span class="gap"></span><svg width="12" height="12"><use href="#i-com"/></svg>No Comments<span class="sp">Share&nbsp;</span><svg width="12" height="12"><use href="#i-share"/></svg></div><div class="thumb" role="img" aria-label="Person jumping over a green meadow under blue sky" style="background:linear-gradient(180deg,#7aa6d8 0%,#a8c8e8 50%,#5a8a3a 55%,#3f6a28 100%)"></div><p>Lorem ipsum dolor sit amet, consecit adipiscing elit, sed do eiusmod tempor incidimen labore n dolorme laboris ni ut ullamc...... <a href="#">Read More</a></p></article>

<article class="card post abs" style="left:84px;top:1522px"><h3>Lorem ipsum dolor sit amet consecit</h3><div class="meta"><svg width="12" height="12"><use href="#i-cal"/></svg>June 18, 2016<span class="gap"></span><svg width="12" height="12"><use href="#i-com"/></svg>No Comments<span class="sp">Share&nbsp;</span><svg width="12" height="12"><use href="#i-share"/></svg></div><div class="thumb" role="img" aria-label="Silhouette jumping at orange sunset" style="background:linear-gradient(180deg,#f08a10,#8a2a05)"></div><p>Lorem ipsum dolor sit amet, consecit adipiscing elit, sed do eiusmod tempor incidimen labore n dolorme laboris ni ut ullamc...... <a href="#">Read More</a></p></article>
<article class="card post abs" style="left:446px;top:1522px"><h3>Lorem ipsum dolor sit amet consecit</h3><div class="meta"><svg width="12" height="12"><use href="#i-cal"/></svg>June 18, 2016<span class="gap"></span><svg width="12" height="12"><use href="#i-com"/></svg>No Comments<span class="sp">Share&nbsp;</span><svg width="12" height="12"><use href="#i-share"/></svg></div><div class="thumb" role="img" aria-label="Woman with open arms among spring leaves" style="background:linear-gradient(135deg,#e8f0c8,#9ab860)"></div><p>Lorem ipsum dolor sit amet, consecit adipiscing elit, sed do eiusmod tempor incidimen labore n dolorme laboris ni ut ullamc...... <a href="#">Read More</a></p></article>

<article class="card post abs" style="left:84px;top:1758px"><h3>Lorem ipsum dolor sit amet consecit</h3><div class="meta"><svg width="12" height="12"><use href="#i-cal"/></svg>June 18, 2016<span class="gap"></span><svg width="12" height="12"><use href="#i-com"/></svg>No Comments<span class="sp">Share&nbsp;</span><svg width="12" height="12"><use href="#i-share"/></svg></div><div class="thumb" role="img" aria-label="Man with raised arms in a sunlit field" style="background:linear-gradient(180deg,#f8e890,#9ab030)"></div><p>Lorem ipsum dolor sit amet, consecit adipiscing elit, sed do eiusmod tempor incidimen labore n dolorme laboris ni ut ullamc...... <a href="#">Read More</a></p></article>
<article class="card post abs" style="left:446px;top:1758px"><h3>Lorem ipsum dolor sit amet consecit</h3><div class="meta"><svg width="12" height="12"><use href="#i-cal"/></svg>June 18, 2016<span class="gap"></span><svg width="12" height="12"><use href="#i-com"/></svg>No Comments<span class="sp">Share&nbsp;</span><svg width="12" height="12"><use href="#i-share"/></svg></div><div class="thumb" role="img" aria-label="Smiling red-haired woman close up" style="background:linear-gradient(135deg,#e8a070,#b85a30)"></div><p>Lorem ipsum dolor sit amet, consecit adipiscing elit, sed do eiusmod tempor incidimen labore n dolorme laboris ni ut ullamc...... <a href="#">Read More</a></p></article>

<aside class="card widget newsletter abs">
  <h4>Newsletter Sign Up</h4>
  <div class="email">Enter Your Email Address</div>
  <a class="btn" href="#">SUBSCRIBE</a>
</aside>

<aside class="card widget tabs-box abs">
  <div class="tabs"><span class="on">Page Views</span><span>Social Shares#</span><span>Comments</span></div>
  <div class="pop"><div class="ph" role="img" aria-label="Woman in a green field" style="background:linear-gradient(135deg,#b8d080,#6a9a40)"></div><p>Lorem ipsum dolor sit ame consectetuer adipiscing Dolor sit almet</p></div>
  <div class="pop"><div class="ph" role="img" aria-label="Woman in a yellow dress" style="background:linear-gradient(135deg,#f4f0e0,#e0c040)"></div><p>Lorem ipsum dolor sit ame consectetuer adipiscing Dolor sit almet</p></div>
  <div class="pop"><div class="ph" role="img" aria-label="Portrait of a smiling man" style="background:linear-gradient(135deg,#e0e0e0,#9a8a7a)"></div><p>Lorem ipsum dolor sit ame consectetuer adipiscing Dolor sit almet</p></div>
  <a class="more view-all" href="#">View All &gt;&gt;</a>
</aside>

<aside class="card widget follow abs">
  <h4>Follow Us</h4>
  <div class="follow-row"><span></span><span></span><span></span><span></span><span></span></div>
</aside>

<aside class="card widget archives abs">
  <h4>Archives</h4>
  <ul><li>July 2016</li><li>June 2016</li><li>May 2016</li><li>April 2016</li><li>March 2016</li><li>February 2016</li><li>January 2016</li></ul>
</aside>

<aside class="card widget tags abs">
  <h4>Popular Tags</h4>
  <div class="tag-list"><span>SIT</span><span>DOLOR</span><span>ALMETSIT</span><span>DOLOR</span><span>ELIT</span><span>SIT</span><span>ELIT</span><span>ALMETS</span></div>
</aside>

<div class="ad abs" role="img" aria-label="Advertisement: pickup truck at dusk with open door"></div>

<section class="about abs">
  <div class="about-photo abs" role="img" aria-label="Portrait of the blog author, a smiling man in a light shirt"></div>
  <h2 class="abs">About Me</h2>
  <p class="abs">Lorem ipsum dolor sit amet, consectetuer adipiscing elit, sed diam nonummy nibh euismod alme tincidunt ut laoreet dolore magna aliquam erat volutpat. Ut wisi enim ad minim veniam, quis dol nostrud exerci tation ullamcorper suscipit lobortis nisl ut aliquip ex ea commodo consequat list Duis autem vel eum iriure dolor in hendrerit in vulputate velit esse molestie consequat, vel alm illum dolore eu feugiat nulla facilisis at vero eros et accumsan et iusto odio dignissim qui blandit illum dolore eu feugiat nulla facilisis at vero eros et accumsan et iusto odio dignissim qui blandit praesent luptatum zzril delenit augue duis dolore te feugait nulla facilisi.</p>
  <a class="more abs" href="#">Read More</a>
</section>

<footer class="footer abs">Copyright © 2016 Tandem K. All Rights Reserved.</footer>
</body>
</html>
```